A design led business card for the construction industry

High-end business card to match logo. White logo on dark grey/off black to the front. Matching dark font on white to back, possibly with logo design again.

We offer construction and project management services to commercial and private clients in the UK. Projetcs range from newbuilds, conversion of listed buildings and refurbishments and extensions of existing homes. Our focus is on quality and attention to detail using the highest skills.

Contact Information for Business Card

Name; Dorian Keble BSc
Position; Project Manager
Mobile; 07962 408 175
Tel; 01632 960457
email; dorian@stonevale.co.uk
web; www.stonevale.co.uk
Address; Wendmoor on Calde, KX4 7PW

Colors

Designer to choose only greyscale colors for use in the design.

Requirements
Must have
• To include the below description of the business,

CONSTRUCTION - PROJECT MANAGEMENT
Nice to have
• The posibility of the top back of the card being used as a ruler. So will have a measurement to scale in mm or an architect scale of 1:50
Should not have
• Should not be portrait

```html
<!DOCTYPE html>
<html lang="en">
<head>
<meta charset="utf-8">
<title>Stonevale — Business Card</title>
<link rel="stylesheet" href="https://fonts.googleapis.com/css2?family=Arimo:wght@400;700&display=swap">
<style>
  :root {
    --backdrop: #858585;
    --card: #1d1c1b;
    --ink: #ffffff;
    --rule: #4a4947;
    --mark: #8c8c8c;
  }
  * { margin: 0; padding: 0; box-sizing: border-box; }
  html, body {
    width: 1093px;
    height: 1200px;
    overflow: hidden;
    background: var(--backdrop);
    font-family: "Arimo", Arial, sans-serif;
    color: var(--ink);
  }
  .card {
    position: absolute;
    left: 264px;
    width: 580px;
    height: 357px;
    background: var(--card);
    text-align: center;
  }
  .card--contact { top: 226px; }
  .card--brand { top: 620px; }

  .contact-name {
    position: absolute;
    top: 80px; left: 0; right: 0;
    font-size: 19px;
    line-height: 22px;
  }
  .contact-name strong { font-weight: 700; }
  .contact-role {
    position: absolute;
    top: 101px; left: 0; right: 0;
    font-size: 16px;
    line-height: 20px;
  }
  .rule {
    position: absolute;
    left: 231px;
    width: 117px;
    height: 1px;
    background: var(--rule);
  }
  .rule--top { top: 134px; }
  .rule--bottom { top: 240px; }
  .contact-list {
    position: absolute;
    top: 145px; left: 0; right: 0;
    list-style: none;
    font-size: 16.5px;
    line-height: 20.8px;
  }
  .contact-list b { font-weight: 700; }
  .contact-address {
    position: absolute;
    top: 253px; left: 0; right: 0;
    font-size: 16.5px;
    line-height: 20px;
  }

  .brand-square {
    position: absolute;
    top: 78px;
    left: 230px;
    width: 120px;
    height: 120px;
    border: 2px solid var(--mark);
  }
  .brand-name {
    position: absolute;
    top: 218px; left: 0; right: 0;
    font-size: 26px;
    line-height: 30px;
    font-weight: 400;
    letter-spacing: 18px;
    padding-left: 18px;
    color: var(--mark);
  }
  .brand-tagline {
    position: absolute;
    top: 264px; left: 0; right: 0;
    font-size: 14px;
    line-height: 18px;
  }
</style>
</head>
<body>
  <section class="card card--contact">
    <p class="contact-name"><strong>DORIAN KEBLE</strong> BSc</p>
    <p class="contact-role">Project Manager</p>
    <div class="rule rule--top"></div>
    <ul class="contact-list">
      <li><b>P:</b> 07962 408 175</li>
      <li><b>M:</b> 01632 960457</li>
      <li><b>E:</b> dorian@stonevale.co.uk</li>
      <li><b>W:</b> www.stonevale.co.uk</li>
    </ul>
    <div class="rule rule--bottom"></div>
    <p class="contact-address">Wendmoor on Calde, KX4 7PW</p>
  </section>

  <section class="card card--brand">
    <div class="brand-square"></div>
    <p class="brand-name">STONEVALE</p>
    <p class="brand-tagline">CONSTRUCTION - PROJECT MANAGEMENT</p>
  </section>
</body>
</html>
```